Website Design for Harbor Guidance

I am looking to create a website to help military members who are currently serving or have served to have a mentor. The military does an awful job and providing or offering a mentor program. People need someone they can come to with career advice with promotions, networking, building resumes, and pinging ideas off of on the occasion. I want a place where active and separated military members can come to, sign up and pick a program of offerings that make sense. They would register annually, pay for a membership package (can choose up to three) and then get support they need. Annual registration fees would be as follows and they would need to send payment through Paypal or other electronic means (credit card, eft, paypal, echeck, whatever).

I envision some type of registration that centers around the packages offered - this will be where the revision comes in once the framework is completed.

I am looking for very creative designs, and content, given the above, with verbiage around mentorship program. Please be creative for the design, and also put together three packages and price points for them three packages - put together what it would include in each package. We can modify as necessary during revisions. Final design should communicate military members in uniform with corporate leaders, something warm and inviting are important. I also want the abiity to really get this adversited and in the market for people to stumble across it easily.

I have purchased the domain already - harborguidance.com

Target Market(s)

Military, Veterans

Number of Pages Required

1 page

Requirements
Must have
• Military member with corporate look
• Modern and wide
• Warm and inviting
• Registration with ability to collect through PayPal, eCheck, Credit Card, etc)
• Creative design and content for the website based on what is described in the description
• About Section which has information about leadership team
• Contact Us
• Register
• 3 creative packages of what would be included (design this and the content keeping in mind the description)
• Content and the framework
• Some type of packages to consider (just examples but also needs mentoring options:
• https://www.careerdraftsmithy.com/
• https://www.cvbeacon.com/
• We are not going to ba resume writing service but we will offer it as part of our solution - I really want it to be focused around mentorship for job development, professional advice, interacting with peers, managers, leaders (using military acronyms like Supervisors and Leaders NCO's, Officers, etc)
• Blog so we can post topics and interact and respond to questions people have etc

```html
<!DOCTYPE html>
<html lang="en">
<head>
<meta charset="utf-8">
<title>Harbor Guidance — Mentorship for Military Members</title>
<link rel="stylesheet" href="https://fonts.googleapis.com/css2?family=Roboto+Condensed:wght@400;700&family=Open+Sans:wght@400;600&family=Oswald:wght@500&display=swap">
<style>
:root{
  --brand-blue:#1a73b8;
  --maroon:#8c1a4b;
  --maroon-deep:#74133d;
  --navy:#0e4a70;
  --ink:#222;
  --body:#555;
  --muted:#777;
  --footer:#1d1d1d;
  --footer-text:#cfcfcf;
  --white:#fff;
}
*{margin:0;padding:0;box-sizing:border-box}
html,body{width:1200px;height:3197px;overflow:hidden}
body{font-family:'Open Sans',sans-serif;color:var(--body);background:var(--white);position:relative}
.abs{position:absolute}
h1,h2,h3,h4,.nav a,.brand{font-family:'Roboto Condensed',sans-serif}

/* header */
.topline{position:absolute;left:0;top:0;width:1200px;height:4px;background:var(--maroon)}
.site-header{position:absolute;left:0;top:4px;width:1200px;height:118px}
.brand{position:absolute;left:92px;top:40px;font-size:36px;font-weight:700;color:var(--brand-blue);letter-spacing:.2px}
.nav{position:absolute;top:50px;left:0;width:1200px}
.nav a{position:absolute;font-family:'Open Sans',sans-serif;font-size:18px;color:#333;text-decoration:none}
.nav a.active{color:var(--maroon)}
.search{position:absolute;left:1085px;top:52px}

/* hero */
.hero{position:absolute;left:0;top:122px;width:1200px;height:511px}
.hero-photo{position:absolute;inset:0;background:linear-gradient(90deg,#6f7f86 0%,#98a5a8 22%,#c9ced1 45%,#e6e9eb 65%,#dde1e4 100%)}
.hero-title{position:absolute;left:727px;top:185px;font-family:'Oswald',sans-serif;font-weight:500;font-size:50px;color:var(--maroon);letter-spacing:.5px}
.hero-sub{position:absolute;left:755px;top:250px;font-family:'Roboto Condensed',sans-serif;font-size:34px;color:#1b5f8e}
.btn-register{position:absolute;left:828px;top:315px;width:121px;height:44px;border:2px solid #333;border-radius:3px;background:rgba(255,255,255,.6);font-family:'Roboto Condensed',sans-serif;font-size:22px;color:#222;display:flex;align-items:center;justify-content:center}
.slide-arrow{position:absolute;top:264px;width:28px;height:28px;border-radius:50%;background:#6c6c6c;display:flex;align-items:center;justify-content:center}

/* welcome */
.welcome{position:absolute;left:0;top:633px;width:1200px;height:373px;text-align:center}
.section-title{font-size:34px;font-weight:400;color:var(--ink)}
.welcome .section-title{position:absolute;left:0;width:1200px;top:76px}
.welcome p{position:absolute;left:215px;width:770px;top:135px;font-size:14.5px;line-height:26px;color:var(--muted)}
.signup{position:absolute;top:239px;height:47px;color:var(--white);font-family:'Roboto Condensed',sans-serif;font-size:17px;display:flex;align-items:center;justify-content:center;border-radius:2px}
.signup.active{left:401px;width:196px;background:var(--brand-blue)}
.signup.veteran{left:606px;width:196px;background:var(--maroon)}

/* what we do */
.what-we-do{position:absolute;left:0;top:1006px;width:1200px;height:456px;overflow:hidden}
.wwd-photo{position:absolute;inset:0;background:linear-gradient(110deg,#8a8578 0%,#b3ada1 45%,#d8d6d2 70%,#9aa6b3 100%)}
.wwd-panel{position:absolute;inset:0;clip-path:polygon(0 0,770px 0,615px 100%,0 100%);background:linear-gradient(135deg,#0c4468 0%,#14608d 40%,#0d4b74 70%,#0a3a5c 100%)}
.wwd-panel h2{position:absolute;left:89px;top:70px;font-size:34px;font-weight:400;color:var(--white)}
.wwd-panel p{position:absolute;left:89px;top:126px;width:525px;font-size:15.5px;line-height:29px;color:var(--white);text-align:justify}
.btn-outline{position:absolute;left:89px;top:314px;width:121px;height:42px;border:1.5px solid var(--white);border-radius:3px;color:var(--white);font-size:15px;display:flex;align-items:center;justify-content:center;gap:5px}

/* packages */
.packages{position:absolute;left:0;top:1462px;width:1200px;height:500px}
.packages .section-title{position:absolute;left:0;width:1200px;text-align:center;top:102px}
.package{position:absolute;top:200px;width:300px;text-align:center}
.package svg{display:block;margin:0 auto}
.package h3{margin-top:30px;font-family:'Open Sans',sans-serif;font-weight:400;font-size:19px;color:var(--ink)}
.package p{margin:14px auto 0;width:230px;font-size:14.5px;line-height:25px;color:#888}
.learn{display:block;margin-top:12px;font-size:13px;color:#1f3d5a}

/* offer */
.offer{position:absolute;left:0;top:1962px;width:1200px;height:500px;color:var(--white)}
.offer-bg{position:absolute;inset:0;background:radial-gradient(ellipse at 50% 40%,#9a2457 0%,#8a1a4b 55%,#74133d 100%)}
.offer .section-title{position:absolute;left:0;width:1200px;text-align:center;top:64px;color:var(--white)}
.offer-item{position:absolute;top:164px;width:260px;text-align:center}
.offer-circle{width:112px;height:112px;border:3px solid var(--white);border-radius:50%;margin:0 auto;display:flex;align-items:center;justify-content:center}
.offer-item h3{margin-top:26px;font-family:'Open Sans',sans-serif;font-size:20px;font-weight:400}
.offer-item p{margin:10px auto 0;width:220px;font-size:14px;line-height:22px}
.offer-item .learn{color:var(--white);font-size:14px;margin-top:12px}
.offer-arrow{position:absolute;top:272px}

/* news */
.news{position:absolute;left:0;top:2462px;width:1200px;height:430px}
.news .section-title{position:absolute;left:0;width:1200px;text-align:center;top:88px}
.news-card{position:absolute;top:195px;width:490px;height:141px}
.news-photo{position:absolute;left:0;top:0;width:162px;height:141px}
.news-body{position:absolute;left:179px;top:8px;width:298px}
.news-body h4{font-family:'Open Sans',sans-serif;font-weight:400;font-size:14.5px;color:#333}
.news-date{font-size:12px;color:#333;margin-top:8px}
.news-body p{font-size:12.5px;line-height:19px;text-align:justify;margin-top:6px}
.read-more{display:block;font-size:12.5px;color:var(--maroon);margin-top:8px}

/* footer */
.site-footer{position:absolute;left:0;top:2892px;width:1200px;height:305px;background:var(--footer);color:var(--footer-text)}
.footer-brand{position:absolute;left:86px;top:122px;font-family:'Roboto Condensed',sans-serif;font-weight:700;font-size:28px;color:var(--brand-blue)}
.footer-col h4{font-family:'Open Sans',sans-serif;font-weight:400;font-size:13.5px;color:#e5e5e5;letter-spacing:.3px}
.footer-col{position:absolute;top:56px}
.contact-list{list-style:none;margin-top:22px;font-size:11.5px;line-height:22px}
.contact-list li{display:flex;gap:12px;align-items:flex-start}
.contact-list svg{margin-top:6px;flex:none}
.mail-note{font-size:11.5px;line-height:16px;margin-top:20px;width:210px}
.mail-form{display:flex;margin-top:16px}
.mail-input{width:144px;height:26px;background:var(--white);font-size:11px;color:#999;padding:6px 8px}
.mail-submit{width:59px;height:26px;background:var(--maroon);color:var(--white);font-size:12px;display:flex;align-items:center;justify-content:center}
.social{display:flex;gap:13px;margin-top:30px;margin-left:14px}
.social span{width:26px;height:26px;background:#e8e8e8;border-radius:4px}
.footer-bottom{position:absolute;left:94px;top:254px;font-size:12px;color:#ddd}
.payments{position:absolute;left:866px;top:250px;display:flex;gap:4px}
.payments span{width:45px;height:24px;border-radius:2px}
</style>
</head>
<body>

<div class="topline"></div>
<header class="site-header">
  <div class="brand">Harbor Guidance</div>
  <nav class="nav">
    <a class="active" style="left:450px">Home</a>
    <a style="left:547px">About us</a>
    <a style="left:665px">Services</a>
    <a style="left:771px">What we do</a>
    <a style="left:913px">Blog</a>
    <a style="left:995px">Contact</a>
  </nav>
  <svg class="search" width="24" height="24" viewBox="0 0 24 24" aria-label="Search"><circle cx="10" cy="10" r="7" fill="none" stroke="#111" stroke-width="3"/><line x1="15" y1="15" x2="22" y2="22" stroke="#111" stroke-width="3.5" stroke-linecap="round"/></svg>
</header>

<section class="hero">
  <div class="hero-photo" role="img" aria-label="Photo of a service member in uniform and a civilian mentor talking over a laptop"></div>
  <div class="hero-title">HARBOR GUIDANCE</div>
  <div class="hero-sub">Neque porro quisquam</div>
  <div class="btn-register">Register</div>
  <div class="slide-arrow" style="left:72px"><svg width="12" height="12" viewBox="0 0 12 12"><path d="M8 1 3 6l5 5" fill="none" stroke="#fff" stroke-width="2"/></svg></div>
  <div class="slide-arrow" style="left:1100px"><svg width="12" height="12" viewBox="0 0 12 12"><path d="M4 1l5 5-5 5" fill="none" stroke="#fff" stroke-width="2"/></svg></div>
</section>

<section class="welcome">
  <h1 class="section-title">Welcome to Harbor Guidance</h1>
  <p>It is a long established fact that a reader will be distracted by the readable content of a page when looking at its layout. The point of using Lorem Ipsum is that it has a more-or-less normal distribution of letters, as opposed to using 'Content here, content here', making it look like readable English.</p>
  <div class="signup active">Active mebers sign up</div>
  <div class="signup veteran">Military member sign up</div>
</section>

<section class="what-we-do">
  <div class="wwd-photo" role="img" aria-label="Photo of a uniformed soldier mentoring a corporate professional at a laptop"></div>
  <div class="wwd-panel">
    <h2>What We Do</h2>
    <p>It is a long established fact that a reader will be distracted by the readable content of a page when looking at its layout. The point of using Lorem Ipsum is that it has a more-or-less normal distribution of letters, as opposed to using 'Content here, content here', making it look like readable English. Many desktop publishing packages and web page editors now use Lorem Ipsum as their default model text,</p>
    <div class="btn-outline">Read More <svg width="9" height="9" viewBox="0 0 9 9"><path d="M1 1l3 3.5L1 8M5 1l3 3.5L5 8" fill="none" stroke="#fff" stroke-width="1.5"/></svg></div>
  </div>
</section>

<section class="packages">
  <h2 class="section-title">Our Packages</h2>
  <div class="package" style="left:128px">
    <svg width="62" height="66" viewBox="0 0 62 66"><circle cx="31" cy="17" r="15" fill="var(--brand-blue)"/><path d="M2 66V52c0-12 10-18 29-18s29 6 29 18v14z" fill="var(--brand-blue)"/></svg>
    <h3>Professional – $190</h3>
    <p>It is a long established fact that a reader will be distracted by the</p>
    <span class="learn">Learn More -&gt;</span>
  </div>
  <div class="package" style="left:446px">
    <svg width="86" height="66" viewBox="0 0 86 66"><path d="M3 0v63h83" fill="none" stroke="var(--brand-blue)" stroke-width="5"/><rect x="14" y="36" width="11" height="22" fill="var(--brand-blue)"/><rect x="30" y="24" width="11" height="34" fill="var(--brand-blue)"/><rect x="46" y="30" width="11" height="28" fill="var(--brand-blue)"/><rect x="62" y="14" width="11" height="44" fill="var(--brand-blue)"/></svg>
    <h3>Executive – $230</h3>
    <p>It is a long established fact that a reader will be distracted by the</p>
    <span class="learn">Learn More -&gt;</span>
  </div>
  <div class="package" style="left:756px">
    <svg width="70" height="62" viewBox="0 0 70 62"><path d="M24 12V5h22v7" fill="none" stroke="var(--brand-blue)" stroke-width="5"/><rect x="0" y="12" width="70" height="50" rx="6" fill="var(--brand-blue)"/><rect x="13" y="12" width="4" height="50" fill="#fff"/><rect x="53" y="12" width="4" height="50" fill="#fff"/></svg>
    <h3>Entry-Level – $150</h3>
    <p>It is a long established fact that a reader will be distracted by the</p>
    <span class="learn">Learn More -&gt;</span>
  </div>
</section>

<section class="offer">
  <div class="offer-bg" role="img" aria-label="Muted photo of a server room under a maroon overlay"></div>
  <h2 class="section-title">We Offer</h2>
  <svg class="offer-arrow" style="left:62px" width="18" height="34" viewBox="0 0 18 34"><path d="M16 2 2 17l14 15" fill="none" stroke="#fff" stroke-width="2"/></svg>
  <svg class="offer-arrow" style="left:1124px" width="18" height="34" viewBox="0 0 18 34"><path d="M2 2l14 15L2 32" fill="none" stroke="#fff" stroke-width="2"/></svg>

  <div class="offer-item" style="left:81px">
    <div class="offer-circle"><svg width="34" height="42" viewBox="0 0 34 42"><path d="M0 0h23l11 11v31H0z" fill="#fff"/><path d="M23 0v11h11" fill="#c9c9c9"/><rect x="7" y="18" width="20" height="3" fill="var(--maroon)"/><rect x="7" y="25" width="20" height="3" fill="var(--maroon)"/><rect x="7" y="32" width="14" height="3" fill="var(--maroon)"/></svg></div>
    <h3>Job development</h3>
    <p>Let Keelstone Advisory find you the perfect home loan.</p>
    <span class="learn">Learn More -&gt;</span>
  </div>
  <div class="offer-item" style="left:344px">
    <div class="offer-circle"><svg width="46" height="38" viewBox="0 0 46 38"><circle cx="23" cy="9" r="7" fill="#fff"/><circle cx="8" cy="13" r="5" fill="#fff"/><circle cx="38" cy="13" r="5" fill="#fff"/><path d="M12 36c0-12 5-17 11-17s11 5 11 17z" fill="#fff"/><path d="M0 34c0-9 3-13 8-13 3 0 5 1 6 3-2 3-3 6-3 10z" fill="#fff"/><path d="M46 34c0-9-3-13-8-13-3 0-5 1-6 3 2 3 3 6 3 10z" fill="#fff"/></svg></div>
    <h3>Professional advice</h3>
    <p>Our experienced and fully qualified accountants</p>
    <span class="learn">Learn More -&gt;</span>
  </div>
  <div class="offer-item" style="left:605px">
    <div class="offer-circle"><svg width="46" height="40" viewBox="0 0 46 40"><path d="M23 3C11 3 3 10 3 18c0 5 3 9 7 12l-3 8 10-5c2 .5 4 .8 6 .8 12 0 20-7 20-15.8S35 3 23 3z" fill="none" stroke="#fff" stroke-width="3.5"/></svg></div>
    <h3>Managers</h3>
    <p>Keelstone Advisory have a thor-ough understanding</p>
    <span class="learn">Learn More -&gt;</span>
  </div>
  <div class="offer-item" style="left:869px">
    <div class="offer-circle"><svg width="48" height="48" viewBox="0 0 48 48"><circle cx="24" cy="24" r="19" fill="none" stroke="#fff" stroke-width="7"/><circle cx="24" cy="24" r="8" fill="none" stroke="#fff" stroke-width="3"/><g stroke="var(--maroon)" stroke-width="4"><line x1="10" y1="10" x2="17" y2="17"/><line x1="38" y1="10" x2="31" y2="17"/><line x1="10" y1="38" x2="17" y2="31"/><line x1="38" y1="38" x2="31" y2="31"/></g></svg></div>
    <h3>Leaders</h3>
    <p>We strengthen the financial standing of our clients</p>
    <span class="learn">Learn More -&gt;</span>
  </div>
</section>

<section class="news">
  <h2 class="section-title">Latest News</h2>
  <article class="news-card" style="left:101px">
    <div class="news-photo" role="img" aria-label="Photo of a service member working at a laptop" style="background:linear-gradient(135deg,#3c4a52,#7c8a8c 55%,#a49c84)"></div>
    <div class="news-body">
      <h4>Nemo Enim Ipsam Volup</h4>
      <div class="news-date">09-07-2017</div>
      <p>Lorem Ipsum has been the industry's standard dummy text ever since the 1500s, when an unknown printer took a galley of type</p>
      <span class="read-more">Read More &gt;&gt;</span>
    </div>
  </article>
  <article class="news-card" style="left:638px">
    <div class="news-photo" role="img" aria-label="Photo of a soldier in a briefing room" style="background:linear-gradient(135deg,#1d2a38,#3e5a72 55%,#5e6b60)"></div>
    <div class="news-body">
      <h4>Nemo Enim Ipsam Volup</h4>
      <div class="news-date">09-07-2017</div>
      <p>Lorem Ipsum has been the industry's standard dummy text ever since the 1500s, when an unknown printer took a galley of type</p>
      <span class="read-more">Read More &gt;&gt;</span>
    </div>
  </article>
</section>

<footer class="site-footer">
  <div class="footer-brand">Harbor Guidance</div>
  <div class="footer-col" style="left:384px">
    <h4>CONTACT US</h4>
    <ul class="contact-list">
      <li><svg width="9" height="12" viewBox="0 0 9 12"><path d="M4.5 0C2 0 0 2 0 4.5 0 8 4.5 12 4.5 12S9 8 9 4.5C9 2 7 0 4.5 0z" fill="#ddd"/><circle cx="4.5" cy="4.5" r="1.6" fill="#1d1d1d"/></svg><span>48 Larkspur Lane<br>Millbrook, ON K0L 2T0</span></li>
      <li><svg width="10" height="10" viewBox="0 0 10 10"><path d="M2 0l2 2.5-1.2 1.3c.7 1.4 1.8 2.5 3.2 3.2L7.3 5.8 10 8 8.5 10C4 10 0 6 0 1.5z" fill="#ddd"/></svg><span>+1-555-014-2290</span></li>
      <li><svg width="11" height="8" viewBox="0 0 11 8"><rect width="11" height="8" fill="#ddd"/><path d="M0 0l5.5 4.5L11 0" fill="none" stroke="#1d1d1d"/></svg><span>hello@harborguidance.com</span></li>
    </ul>
  </div>
  <div class="footer-col" style="left:648px">
    <h4>JOIN OUR MAILING LIST</h4>
    <p class="mail-note">Your about us information would fit here nicely.</p>
    <div class="mail-form"><div class="mail-input">Email address</div><div class="mail-submit">Submit</div></div>
  </div>
  <div class="footer-col" style="left:937px">
    <h4>FOLLOW US OUT THERE</h4>
    <div class="social"><span></span><span></span><span></span><span></span></div>
  </div>
  <div class="footer-bottom">Copyright © 2018 All Rights Reserved</div>
  <div class="payments">
    <span style="background:#2a6fb0"></span>
    <span style="background:#7a2a7c"></span>
    <span style="background:#1b4fa0"></span>
    <span style="background:#e0701f"></span>
    <span style="background:#e9e9e9"></span>
  </div>
</footer>

</body>
</html>
```